Tech business card design

We need an amazing business card design for our new business 'Pexla' a marketing tech startup based in Sydney, Australia. We provide an online marketplace for businesses to search and buy advertising media, connect with service providers and learn more about marketing. We wish to communicate 'cool tech', reliability and professionalism and design based around our logo.

Target Market(s)

Business Owners

Contact Information for Business Card

Name
Position
Email Address
Website
Phone Number

Font styles to use
Other font styles liked:
• Avenir & Avenir Next

Colors

Designer to choose colors to be used in the design.

```html
<!DOCTYPE html>
<html lang="en">
<head>
<meta charset="utf-8">
<title>Pexla Business Card</title>
<link rel="stylesheet" href="https://fonts.googleapis.com/css2?family=Nunito+Sans:wght@400;800;900&display=swap">
<style>
  :root {
    --bg: #e4e5e8;
    --navy: #1d1b4c;
    --navy-deep: #17153f;
    --navy-soft: #25235a;
    --white: #ffffff;
    --ink: #1d1b4c;
    --text: #2a2850;
  }
  * { box-sizing: border-box; margin: 0; padding: 0; }
  html, body { width: 1200px; height: 800px; overflow: hidden; }
  body {
    background: var(--bg);
    font-family: "Nunito Sans", sans-serif;
    position: relative;
  }
  .card {
    position: absolute;
    top: 241px;
    width: 520px;
    height: 318px;
    border-radius: 4px;
    box-shadow: 0 10px 28px rgba(20, 20, 40, 0.18);
    overflow: hidden;
  }
  .card--back { left: 50px; background: var(--navy); }
  .card--front { left: 630px; background: var(--white); }

  .back-pattern {
    position: absolute; inset: 0;
    background: linear-gradient(135deg, var(--navy-soft) 0%, var(--navy) 50%, var(--navy-deep) 100%);
  }
  .back-wordmark {
    position: absolute;
    left: 0; right: 0; top: 50%;
    transform: translateY(-50%);
    text-align: center;
    color: var(--white);
    font-weight: 900;
    font-size: 46px;
    letter-spacing: -1px;
  }

  .front-wordmark {
    position: absolute;
    left: 0; right: 0; top: 50px;
    text-align: center;
    color: var(--ink);
    font-weight: 900;
    font-size: 110px;
    line-height: 1;
    letter-spacing: -3px;
  }
  .front-details {
    position: absolute;
    top: 200px; left: 0; right: 0;
    display: flex;
    justify-content: center;
    align-items: stretch;
    gap: 18px;
    color: var(--text);
  }
  .person { text-align: right; padding-top: 4px; }
  .person__name { font-weight: 800; font-size: 17px; }
  .person__role { font-weight: 400; font-size: 16px; }
  .divider { width: 1px; background: var(--text); }
  .contact { list-style: none; font-size: 14.5px; line-height: 1.55; }
  .contact li { display: flex; align-items: center; gap: 8px; }
  .contact svg { width: 13px; height: 13px; flex: none; }
</style>
</head>
<body>
  <section class="card card--back" aria-label="Card back">
    <div class="back-pattern" role="img" aria-label="Faint repeating brand name pattern in dark navy tones"></div>
    <div class="back-wordmark">pexla</div>
  </section>

  <section class="card card--front" aria-label="Card front">
    <div class="front-wordmark">pexla</div>
    <div class="front-details">
      <div class="person">
        <div class="person__name">Marcus Dale</div>
        <div class="person__role">Founder, Director</div>
      </div>
      <div class="divider"></div>
      <ul class="contact">
        <li>
          <svg viewBox="0 0 16 16" aria-hidden="true"><path fill="var(--ink)" d="M3.6 1.5l2.3 2.6-1.3 1.9c.9 2 2.4 3.6 4.4 4.5l1.9-1.3 2.6 2.3-1.4 2.3C6.7 14.4 1.6 9.3 1.3 3z"/></svg>
          +61 (0)400 555 018
        </li>
        <li>
          <svg viewBox="0 0 16 16" aria-hidden="true"><rect x="1" y="3" width="14" height="10" fill="var(--ink)"/><path d="M1.5 3.5L8 9l6.5-5.5" stroke="#fff" stroke-width="1.3" fill="none"/></svg>
          marcus@pexlamedia.com.au
        </li>
        <li>
          <svg viewBox="0 0 16 16" aria-hidden="true"><circle cx="8" cy="8" r="7" fill="var(--ink)"/><g stroke="#fff" stroke-width="1" fill="none"><ellipse cx="8" cy="8" rx="3" ry="7"/><path d="M1 8h14M2.5 4.5h11M2.5 11.5h11"/></g></svg>
          www.pexlamedia.com.au
        </li>
      </ul>
    </div>
  </section>
</body>
</html>
```